Veldmark Supplies Business Card

Professional business card that stand out to our potential customers. Front and back with clean modern design

Industry/Entity Type

Oil and gas

Contact Information for Business Card

Name, address, website , office phone and cell number

Requirements
Must have
• Editable files for each employee

```html
<!DOCTYPE html>
<html lang="en">
<head>
<meta charset="utf-8">
<title>Veldmark Supplies Business Card</title>
<link href="https://fonts.googleapis.com/css2?family=Montserrat:wght@400;500;800&display=swap" rel="stylesheet">
<style>
  :root {
    --brand-red: #ec1f27;
    --brand-blue: #0cb0d3;
    --ink: #1b1b1b;
    --paper: #ffffff;
    --backdrop: #e6e6e6;
  }
  * { box-sizing: border-box; margin: 0; padding: 0; }
  html, body { width: 1200px; height: 856px; overflow: hidden; }
  body {
    background: var(--backdrop);
    font-family: "Montserrat", sans-serif;
    display: flex;
    align-items: center;
    justify-content: center;
    gap: 40px;
  }
  .card {
    position: relative;
    width: 540px;
    height: 309px;
    overflow: hidden;
    box-shadow: 0 10px 24px rgba(0,0,0,.25);
  }
  .card-front { background: var(--paper); }
  .card-back { background: var(--brand-blue); display: flex; align-items: center; justify-content: center; }

  .front-bands { position: absolute; inset: 0; }

  .wordmark {
    display: flex;
    align-items: center;
    gap: 8px;
    font-weight: 800;
    text-transform: uppercase;
    letter-spacing: .5px;
    line-height: 1;
    white-space: nowrap;
  }
  .wordmark-square { background: var(--brand-red); flex: none; }
  .front-wordmark {
    position: absolute; left: 30px; top: 150px;
    color: var(--brand-red); font-size: 15px;
  }
  .front-wordmark .wordmark-square { width: 13px; height: 13px; background: var(--brand-blue); }
  .back-wordmark { color: var(--paper); font-size: 32px; gap: 14px; }
  .back-wordmark .wordmark-square { width: 30px; height: 30px; }

  .divider-lines { position: absolute; left: 246px; top: 70px; }

  .contact {
    position: absolute; left: 292px; top: 40px;
    color: var(--ink);
  }
  .contact-name {
    color: var(--brand-red); font-weight: 800; font-size: 18px;
    text-transform: uppercase; letter-spacing: .4px;
  }
  .contact-title { font-size: 11px; font-weight: 500; margin-top: 3px; }
  .contact-address { font-size: 11px; line-height: 1.4; margin-top: 12px; }
  .contact-list { list-style: none; margin-top: 10px; font-size: 11px; }
  .contact-list li { display: flex; align-items: center; gap: 7px; height: 18px; }
  .contact-icon {
    width: 13px; height: 13px; background: var(--brand-red);
    display: flex; align-items: center; justify-content: center; flex: none;
  }
  .contact-text { white-space: nowrap; }
  .accent { color: var(--brand-red); }
</style>
</head>
<body>
  <section class="card card-front">
    <svg class="front-bands" width="540" height="309" viewBox="0 0 540 309" aria-hidden="true">
      <polygon points="0,272 365,272 392,238 540,238 540,309 0,309" fill="var(--brand-blue)"/>
      <polygon points="0,261 355,261 363,253 0,253" fill="var(--brand-red)"/>
    </svg>

    <div class="wordmark front-wordmark"><span class="wordmark-square"></span><span>Veldmark Supplies</span></div>

    <svg class="divider-lines" width="40" height="130" viewBox="0 0 40 130" aria-hidden="true">
      <line x1="4" y1="0" x2="4" y2="130" stroke="var(--brand-blue)" stroke-width="1"/>
      <line x1="14" y1="10" x2="14" y2="110" stroke="var(--brand-red)" stroke-width="1"/>
      <line x1="24" y1="20" x2="24" y2="120" stroke="var(--brand-red)" stroke-width="1"/>
    </svg>

    <div class="contact">
      <h1 class="contact-name">Dorran Ellsworth</h1>
      <p class="contact-title">President</p>
      <p class="contact-address">482 Alder Crest Rd, Ste<br>210, Fort Wren, TX 79901</p>
      <ul class="contact-list">
        <li><span class="contact-icon"><svg width="9" height="9" viewBox="0 0 10 10"><path d="M2 1l2 2-1 1.5c.7 1.3 1.3 1.9 2.5 2.5L7 6l2 2-1.5 1.5C4.5 9 1 5.5.5 2.5z" fill="#fff"/></svg></span><span class="contact-text">555-204-3187</span></li>
        <li><span class="contact-icon"><svg width="9" height="9" viewBox="0 0 10 10"><rect x="2.5" y=".5" width="5" height="9" rx="1" fill="none" stroke="#fff"/></svg></span><span class="contact-text">555-318-4420</span></li>
        <li><span class="contact-icon"><svg width="9" height="9" viewBox="0 0 10 10"><rect x=".5" y="2" width="9" height="6" fill="none" stroke="#fff"/><path d="M.5 2L5 5.5 9.5 2" fill="none" stroke="#fff"/></svg></span><span class="contact-text">info@veldmarksupplies.com</span></li>
        <li><span class="contact-icon"><svg width="9" height="9" viewBox="0 0 10 10"><circle cx="5" cy="5" r="4.2" fill="none" stroke="#fff"/><path d="M1 5h8M5 1c-2 2.5-2 5.5 0 8M5 1c2 2.5 2 5.5 0 8" fill="none" stroke="#fff" stroke-width=".8"/></svg></span><span class="contact-text">www.<span class="accent">veldmarksupplies</span>.com</span></li>
      </ul>
    </div>
  </section>

  <section class="card card-back">
    <div class="wordmark back-wordmark"><span class="wordmark-square"></span><span>Veldmark Supplies</span></div>
  </section>
</body>
</html>
```